Educational Management System User Interface (Vantrel Design Concepts)

Hi,I require a 1-page design for an educational management system. The image attached shows all required elements and also their locations. I require the design to be based on vantrel-styled interfaces using elements from: http://prelk.hostvane.io/prelk-kitframe/ & http://kitframenil.com/kitframe-layout/admin . Side menu's should not be too large that they hide the main content of the page.
Sorry very slight addition to the design as per new uploaded file.
I like how the elements of the vantrel loop page are seperated with the background colour and white boxes. This could maybe work in the design as per the uploaded image?
Thanks,
Gideon

```html
<!DOCTYPE html>
<html lang="en">
<head>
<meta charset="utf-8">
<title>Lernit LMS – Teacher Groups</title>
<link rel="stylesheet" href="https://fonts.googleapis.com/css2?family=Figtree:wght@400;500;600;700&display=swap">
<style>
:root{
  --ink:#333;
  --ink-soft:#555;
  --navy:#1b2f5e;
  --muted:#8a8a8a;
  --link:#6f9fcf;
  --icon:#6f9fcf;
  --brand:#2d6db5;
  --line:#e3e3e3;
  --band:#f2f2f2;
  --stage:#e5e5e5;
  --green:#7cbb55;
  --red:#d6453b;
  --online:#34b233;
  --away:#bdbdbd;
  --busy:#e64a2e;
  --leave-bg:#dce8f3;
  --white:#fff;
}
*{box-sizing:border-box;margin:0;padding:0}
html,body{width:1200px;height:950px;overflow:hidden}
body{position:relative;background:var(--white);font-family:"Figtree",Arial,sans-serif;color:var(--ink)}
.abs{position:absolute}

/* header */
.topbar{left:0;top:0;width:1200px;height:82px;background:var(--white);border-bottom:1px solid #d9d9d9}
.brand{left:18px;top:24px;display:flex;align-items:center;gap:10px}
.brand-dot{width:36px;height:36px;border-radius:50%;background:#e9a23b}
.brand-name{font-size:29px;font-weight:600;color:var(--brand);letter-spacing:-.5px}
.top-divider{left:222px;top:0;width:1px;height:72px;background:var(--line)}
.nav-icon{top:26px}
.tools{left:846px;top:0;width:130px;height:81px;background:#f4f4f4}
.badge{left:887px;top:24px;width:20px;height:20px;border-radius:50%;border:1px solid var(--red);color:var(--red);font-size:11px;text-align:center;line-height:18px;background:var(--white)}
.user-name{left:998px;top:33px;font-size:14px;font-weight:500;color:#222}
.user-photo{left:1133px;top:16px;width:53px;height:53px;border-radius:50%;background:radial-gradient(circle at 50% 40%,#b88a78,#3a2a26)}

/* left sidebar */
.sidebar{left:0;top:82px;width:230px;height:868px;background:var(--white);box-shadow:2px 0 4px rgba(0,0,0,.18)}
.role-title{left:0;top:94px;width:230px;text-align:center;font-size:28px;font-weight:600;color:#7fa6cc;letter-spacing:.5px}
.band{left:0;width:230px;height:43px;background:var(--band);font-size:17px;font-weight:500;color:#222;padding:12px 27px}
.group-item{left:0;width:230px;height:38px;border-bottom:1px dashed #d5d5d5;font-size:14px;color:var(--ink-soft);padding:10px 35px}
.group-item svg{position:absolute;right:17px;top:11px}
.btn{left:23px;width:184px;height:28px;color:var(--white);font-size:14px;font-weight:500;text-align:center;line-height:28px;border-radius:2px}
.btn-green{top:356px;background:var(--green)}
.btn-red{top:390px;background:var(--red)}

/* feed */
.stage{left:230px;top:82px;width:716px;height:868px;background:var(--stage)}
.feed{left:253px;top:100px;width:680px;height:850px;background:var(--white);border:1px solid #d6d6d6}
.post{left:0;width:678px;border-bottom:1px solid var(--line)}
.post-avatar{left:27px;width:57px;height:57px;border-radius:5px}
.post-meta{left:101px;font-size:15px;font-weight:700;color:var(--navy)}
.post-meta .date{font-size:13px;font-weight:600;color:var(--muted);margin-left:6px;padding-left:8px;border-left:2px solid #777}
.post-text{left:102px;width:565px;font-size:15px;line-height:20px;color:var(--ink)}
.post-actions{left:102px;display:flex;align-items:center;font-size:15px;color:var(--link)}
.post-actions svg{margin-right:16px}
.post-actions span{margin-left:18px}
.post-actions span:first-of-type{margin-left:4px}

/* right sidebar */
.aside{left:946px;top:82px;width:254px;height:868px;background:var(--white)}
.aside-title{left:969px;font-size:17px;font-weight:500;color:#5c82b3;display:flex;align-items:center;gap:8px}
.scroll-mark{left:1191px;top:110px;width:3px;height:100px;background:#4a86c5}
.member{left:969px;display:flex;align-items:center;gap:11px;font-size:13px;font-weight:600;color:#333}
.thumb{width:36px;height:36px;border-radius:3px;position:relative;flex:none}
.status{position:absolute;right:-4px;bottom:-4px;width:10px;height:10px;border-radius:50%;border:1px solid var(--white)}
.aside-rule{left:946px;top:407px;width:254px;height:1px;background:var(--line)}
.event{left:969px;width:215px;display:flex;align-items:center;gap:11px}
.event b{display:block;font-size:13px;font-weight:600;color:#333}
.event i{display:block;font-style:normal;font-size:12px;font-weight:600;color:var(--muted)}
.event svg{position:absolute;right:0;top:10px}
.leave{left:946px;top:900px;width:254px;height:38px;background:var(--leave-bg);font-size:16px;font-weight:500;color:#2d4f84;padding:9px 22px}
.leave svg{position:absolute;right:22px;top:14px}
</style>
</head>
<body>

<header class="abs topbar"></header>
<div class="abs brand"><span class="brand-dot"></span><span class="brand-name">Lernit LMS</span></div>
<div class="abs top-divider"></div>

<svg class="abs nav-icon" style="left:253px" width="33" height="30" viewBox="0 0 33 30" fill="none" stroke="#6f9fcf" stroke-width="2"><path d="M2 15 16.5 2 31 15"/><path d="M6 12v16h8v-9h5v9h8V12" fill="#6f9fcf" fill-opacity=".25"/></svg>
<svg class="abs nav-icon" style="left:321px" width="30" height="29" viewBox="0 0 30 29" fill="#6f9fcf"><rect x="1" y="4" width="28" height="24" rx="1" fill="none" stroke="#6f9fcf" stroke-width="2"/><rect x="7" y="0" width="3" height="6"/><rect x="20" y="0" width="3" height="6"/><g><rect x="5" y="10" width="4" height="3"/><rect x="11" y="10" width="4" height="3"/><rect x="17" y="10" width="4" height="3"/><rect x="23" y="10" width="3" height="3"/><rect x="5" y="15" width="4" height="3"/><rect x="11" y="15" width="4" height="3"/><rect x="17" y="15" width="4" height="3"/><rect x="23" y="15" width="3" height="3"/><rect x="5" y="20" width="4" height="3"/><rect x="11" y="20" width="4" height="3"/><rect x="17" y="20" width="4" height="3"/></g></svg>
<svg class="abs nav-icon" style="left:386px" width="29" height="29" viewBox="0 0 29 29" fill="none" stroke="#6f9fcf" stroke-width="2"><rect x="1" y="4" width="23" height="23"/><path d="M6 14l6 6L27 2"/></svg>
<svg class="abs nav-icon" style="left:450px;top:28px" width="38" height="27" viewBox="0 0 38 27" fill="none" stroke="#6f9fcf" stroke-width="2"><path d="M1 25V2h11l3 3h16v5"/><path d="M1 25 7 10h30l-6 15z" fill="#6f9fcf" fill-opacity=".25"/></svg>

<div class="abs tools"></div>
<svg class="abs" style="left:874px;top:36px" width="19" height="14" viewBox="0 0 19 14" fill="none" stroke="#888" stroke-width="1.2"><rect x=".6" y=".6" width="17.8" height="12.8"/><path d="M1 1l8.5 7L18 1"/></svg>
<div class="abs badge">2</div>
<svg class="abs" style="left:939px;top:33px" width="15" height="18" viewBox="0 0 15 18" fill="none" stroke="#999" stroke-width="1.2"><path d="M1 3h13M5 3V1h5v2M2.5 3l1 14h8l1-14M6 6v8M9 6v8"/></svg>
<div class="abs user-name">Mara Linden</div>
<div class="abs user-photo" role="img" aria-label="Profile photo of the signed-in teacher"></div>

<nav class="abs sidebar"></nav>
<div class="abs role-title">TEACHER</div>
<div class="abs band" style="top:140px">My Groups</div>
<div class="abs group-item" style="top:184px">Group Name One<svg width="20" height="16" viewBox="0 0 20 16" fill="#6f9fcf"><path d="M0 5h11V0l9 8-9 8v-5H0z"/></svg></div>
<div class="abs group-item" style="top:222px">Group Name Two<svg width="20" height="16" viewBox="0 0 20 16" fill="#6f9fcf"><path d="M0 5h11V0l9 8-9 8v-5H0z"/></svg></div>
<div class="abs group-item" style="top:260px">Group Name Three<svg width="20" height="16" viewBox="0 0 20 16" fill="#6f9fcf"><path d="M0 5h11V0l9 8-9 8v-5H0z"/></svg></div>
<div class="abs group-item" style="top:298px">Group Name 4<svg width="20" height="16" viewBox="0 0 20 16" fill="#6f9fcf"><path d="M0 5h11V0l9 8-9 8v-5H0z"/></svg></div>
<div class="abs btn btn-green">Create New Group</div>
<div class="abs btn btn-red">Join More Groups</div>
<div class="abs band" style="top:437px">Community</div>
<div class="abs group-item" style="top:481px">Study Nook<svg width="20" height="16" viewBox="0 0 20 16" fill="#6f9fcf"><path d="M0 5h11V0l9 8-9 8v-5H0z"/></svg></div>

<main class="abs stage"></main>
<section class="abs feed">
  <article class="abs post" style="top:0;height:207px">
    <div class="abs post-avatar" style="top:18px;background:linear-gradient(160deg,#4d6fa0,#2a2a35)" role="img" aria-label="Member profile photo"></div>
    <div class="abs post-meta" style="top:21px">Tobin Reyes<span class="date">Mar 06, 2014</span></div>
    <p class="abs post-text" style="top:57px">Lorem Ipsum is simply dummy text of the printing and typesetting industry. Lorem Ipsum has been the industry's standard dummy text ever since the 1500s, when an unknown printer took a galley of type and scrambled it to make a type specimen book. It has survived not only five centuries, but also the leap into</p>
    <div class="abs post-actions" style="top:164px"><svg width="15" height="14" viewBox="0 0 15 14" fill="#333"><path d="M9 0l6 5-6 5V7C5 7 2 8 0 13 0 7 3 3 9 3z"/></svg><svg width="19" height="16" viewBox="0 0 19 16" fill="#333"><path d="M9.5 16 1.5 8A4.6 4.6 0 0 1 9.5 2a4.6 4.6 0 0 1 8 6z"/></svg><span>Reply</span><span>Forward</span><span>Delete</span></div>
  </article>
  <article class="abs post" style="top:207px;height:216px">
    <div class="abs post-avatar" style="top:26px;background:linear-gradient(160deg,#c9b39c,#7a5440)" role="img" aria-label="Member profile photo"></div>
    <div class="abs post-meta" style="top:29px">Tobin Reyes<span class="date">Mar 06, 2014</span></div>
    <p class="abs post-text" style="top:66px">Lorem Ipsum is simply dummy text of the printing and typesetting industry. Lorem Ipsum has been the industry's standard dummy text ever since the 1500s, when an unknown printer took a galley of type and scrambled it to make a type specimen book. It has survived not only five centuries, but also the leap into</p>
    <div class="abs post-actions" style="top:173px"><svg width="15" height="14" viewBox="0 0 15 14" fill="#333"><path d="M9 0l6 5-6 5V7C5 7 2 8 0 13 0 7 3 3 9 3z"/></svg><svg width="19" height="16" viewBox="0 0 19 16" fill="#333"><path d="M9.5 16 1.5 8A4.6 4.6 0 0 1 9.5 2a4.6 4.6 0 0 1 8 6z"/></svg><span>Reply</span><span>Forward</span><span>Delete</span></div>
  </article>
  <article class="abs post" style="top:423px;height:215px">
    <div class="abs post-avatar" style="top:25px;background:linear-gradient(160deg,#6f8a5a,#6b4a38)" role="img" aria-label="Member profile photo"></div>
    <div class="abs post-meta" style="top:28px">Tobin Reyes<span class="date">Mar 06, 2014</span></div>
    <p class="abs post-text" style="top:66px">Lorem Ipsum is simply dummy text of the printing and typesetting industry. Lorem Ipsum has been the industry's standard dummy text ever since the 1500s, when an unknown printer took a galley of type and scrambled it to make a type specimen book. It has survived not only five centuries, but also the leap into</p>
    <div class="abs post-actions" style="top:172px"><svg width="15" height="14" viewBox="0 0 15 14" fill="#333"><path d="M9 0l6 5-6 5V7C5 7 2 8 0 13 0 7 3 3 9 3z"/></svg><svg width="19" height="16" viewBox="0 0 19 16" fill="#333"><path d="M9.5 16 1.5 8A4.6 4.6 0 0 1 9.5 2a4.6 4.6 0 0 1 8 6z"/></svg><span>Reply</span><span>Forward</span><span>Delete</span></div>
  </article>
  <article class="abs post" style="top:638px;height:212px;border-bottom:0">
    <div class="abs post-avatar" style="top:28px;background:linear-gradient(160deg,#6f8a5a,#6b4a38)" role="img" aria-label="Member profile photo"></div>
    <div class="abs post-meta" style="top:31px">Tobin Reyes<span class="date">Mar 06, 2014</span></div>
    <p class="abs post-text" style="top:69px">Lorem Ipsum is simply dummy text of the printing and typesetting industry. Lorem Ipsum has been the industry's standard dummy text ever since the 1500s, when an unknown printer took a galley of type and scrambled…</p>
    <div class="abs post-actions" style="top:155px"><svg width="15" height="14" viewBox="0 0 15 14" fill="#333"><path d="M9 0l6 5-6 5V7C5 7 2 8 0 13 0 7 3 3 9 3z"/></svg><svg width="19" height="16" viewBox="0 0 19 16" fill="#333"><path d="M9.5 16 1.5 8A4.6 4.6 0 0 1 9.5 2a4.6 4.6 0 0 1 8 6z"/></svg><span>Reply</span><span>Forward</span><span>Delete</span></div>
  </article>
</section>

<aside class="abs aside"></aside>
<div class="abs scroll-mark"></div>
<div class="abs aside-title" style="top:104px"><svg width="28" height="18" viewBox="0 0 28 18" fill="#8fb0d6"><circle cx="9" cy="5" r="4"/><path d="M1 17c0-5 3.5-7 8-7s8 2 8 7z"/><circle cx="19" cy="5" r="3.5"/><path d="M18 10c5 0 9 2 9 7h-8c0-3-1-5-3-6z"/></svg>Group Members</div>

<div class="abs member" style="top:140px"><div class="thumb" style="background:linear-gradient(#ddd,#777)" role="img" aria-label="Member photo"><span class="status" style="background:var(--online)"></span></div>John Doe</div>
<div class="abs member" style="top:193px"><div class="thumb" style="background:linear-gradient(#7a3b55,#2a1a22)" role="img" aria-label="Member photo"><span class="status" style="background:var(--online)"></span></div>Lorem Ipsum</div>
<div class="abs member" style="top:244px"><div class="thumb" style="background:linear-gradient(#5c6b4c,#3b2c24)" role="img" aria-label="Member photo"><span class="status" style="background:var(--away)"></span></div>Idris Holloway</div>
<div class="abs member" style="top:297px"><div class="thumb" style="background:linear-gradient(#d2b49a,#8a5a40)" role="img" aria-label="Member photo"><span class="status" style="background:var(--busy)"></span></div>Pellcraft</div>
<div class="abs member" style="top:349px"><div class="thumb" style="background:linear-gradient(#e6c7aa,#a0704e)" role="img" aria-label="Member photo"><span class="status" style="background:var(--online)"></span></div>Pellcraft</div>

<div class="abs aside-rule"></div>
<div class="abs aside-title" style="top:427px"><svg width="15" height="16" viewBox="0 0 15 16" fill="#8fb0d6"><rect x="0" y="2" width="15" height="14" rx="1" fill="none" stroke="#8fb0d6" stroke-width="1.5"/><rect x="3" y="0" width="2" height="4"/><rect x="10" y="0" width="2" height="4"/><rect x="3" y="7" width="2" height="2"/><rect x="7" y="7" width="2" height="2"/><rect x="11" y="7" width="2" height="2"/><rect x="3" y="11" width="2" height="2"/><rect x="7" y="11" width="2" height="2"/></svg>UpComing Group Events</div>

<div class="abs event" style="top:463px"><div class="thumb" style="background:linear-gradient(#5b7fb0,#2b2f44)" role="img" aria-label="Member photo"></div><div><b>Noor has joined</b><i>Mar 06, 2014</i></div><svg width="22" height="19" viewBox="0 0 22 19"><path d="M11 0 22 19H0z" fill="#8fb0d6"/><rect x="10" y="6" width="2" height="7" fill="#fff"/><rect x="10" y="14.5" width="2" height="2" fill="#fff"/></svg></div>
<div class="abs event" style="top:524px"><div class="thumb" style="background:linear-gradient(#6f8a5a,#5a3a2a)" role="img" aria-label="Member photo"></div><div><b>Noor has joined</b><i>Mar 06, 2014</i></div><svg width="22" height="19" viewBox="0 0 22 19"><path d="M11 0 22 19H0z" fill="#8fb0d6"/><rect x="10" y="6" width="2" height="7" fill="#fff"/><rect x="10" y="14.5" width="2" height="2" fill="#fff"/></svg></div>
<div class="abs event" style="top:586px"><div class="thumb" style="background:linear-gradient(#ddd,#a4846c)" role="img" aria-label="Studio profile picture"></div><div><b>Brightforge</b><i>Mar 06, 2014</i></div><svg width="22" height="19" viewBox="0 0 22 19"><path d="M11 0 22 19H0z" fill="#8fb0d6"/><rect x="10" y="6" width="2" height="7" fill="#fff"/><rect x="10" y="14.5" width="2" height="2" fill="#fff"/></svg></div>
<div class="abs event" style="top:648px"><div class="thumb" style="background:#e4262f" role="img" aria-label="Studio profile picture"></div><div><b>Keel Studio</b><i>Mar 06, 2014</i></div><svg width="22" height="19" viewBox="0 0 22 19"><path d="M11 0 22 19H0z" fill="#8fb0d6"/><rect x="10" y="6" width="2" height="7" fill="#fff"/><rect x="10" y="14.5" width="2" height="2" fill="#fff"/></svg></div>
<div class="abs event" style="top:709px"><div class="thumb" style="background:linear-gradient(#3fb7b2,#a0704e)" role="img" aria-label="Member photo"></div><div><b>Norden Brand</b><i>Mar 06, 2014</i></div><svg width="22" height="19" viewBox="0 0 22 19"><path d="M11 0 22 19H0z" fill="#8fb0d6"/><rect x="10" y="6" width="2" height="7" fill="#fff"/><rect x="10" y="14.5" width="2" height="2" fill="#fff"/></svg></div>
<div class="abs event" style="top:771px"><div class="thumb" style="background:linear-gradient(#e9b94f,#c98a66)" role="img" aria-label="Member photo"></div><div><b>Noor has joined</b><i>Mar 06, 2014</i></div><svg width="22" height="19" viewBox="0 0 22 19"><path d="M11 0 22 19H0z" fill="#8fb0d6"/><rect x="10" y="6" width="2" height="7" fill="#fff"/><rect x="10" y="14.5" width="2" height="2" fill="#fff"/></svg></div>
<div class="abs event" style="top:833px"><div class="thumb" style="background:linear-gradient(#3b2a26,#a0704e)" role="img" aria-label="Member photo"></div><div><b>Noor has joined</b><i>Mar 06, 2014</i></div><svg width="22" height="19" viewBox="0 0 22 19"><path d="M11 0 22 19H0z" fill="#8fb0d6"/><rect x="10" y="6" width="2" height="7" fill="#fff"/><rect x="10" y="14.5" width="2" height="2" fill="#fff"/></svg></div>

<div class="abs leave">Request to Leave Group<svg width="6" height="10" viewBox="0 0 6 10" fill="#2d4f84"><path d="M0 0l6 5-6 5z"/></svg></div>

</body>
</html>
```